Postcard design to acquire new clients for my Property Management Company

I'm looking for a postcard design that I can send to prospective clients detailing information about my company and services.
Postcard should be eye catching and contain information from www.bramblecrestpm.com. I've provided a few screen shots for the most important information and my logo.
Target Market(s)
Real Estate
Industry/Entity Type
Real Estate
Font styles to use
Sans Serif
Requirements
Must have
- Must be eye catching!! this will be a direct mail piece - I'd like for the card to be read and not tossed in the trash immediately.
Design que from the logo.
A place to write / print the receipts name and address.
our physical address - 2387 Hollow Pine Road, Lubbock, TX 79852.
Should not have
- the contact information on the business card is not accurate - please use info from website.

```html
<!DOCTYPE html>
<html lang="en">
<head>
<meta charset="UTF-8">
<title>Bramblecrest Property Management – Postcard</title>
<link href="https://fonts.googleapis.com/css2?family=Montserrat:wght@400;500;600;700&family=Oswald:wght@500&display=swap" rel="stylesheet">
<style>
  :root {
    --brand-blue: #1f5b93;
    --brand-blue-dark: #1a4f80;
    --ink-grey: #8c8c8c;
    --soft-grey: #a9a9a9;
    --card-white: #ffffff;
    --page-bg: #eef0f2;
    --card-shadow: rgba(0,0,0,0.18);
  }
  * { margin: 0; padding: 0; box-sizing: border-box; }
  html, body { width: 1052px; height: 1200px; overflow: hidden; }
  body { background: var(--page-bg); font-family: "Montserrat", sans-serif; position: relative; }

  .postcard {
    position: absolute; left: 96px; width: 860px; height: 568px;
    background: var(--card-white);
    border-top: 9px solid var(--brand-blue);
    box-shadow: 0 6px 0 #c9c9c9, 0 10px 18px var(--card-shadow);
    overflow: hidden;
  }
  .postcard--front { top: 20px; }
  .postcard--back { top: 612px; }

  /* wordmark */
  .wordmark { position: absolute; text-align: center; color: var(--brand-blue); }
  .wordmark__name { display: block; font-weight: 700; letter-spacing: 0.2em; line-height: 1; }
  .wordmark__tag { display: block; font-weight: 500; letter-spacing: 0.22em; line-height: 1; }
  .postcard--front .wordmark { left: 0; right: 0; top: 22px; }
  .postcard--front .wordmark__name { font-size: 36px; }
  .postcard--front .wordmark__tag { font-size: 17px; margin-top: 10px; }

  .hero-photo {
    position: absolute; left: 0; top: 105px; width: 860px; height: 296px;
    background: linear-gradient(100deg, #6f86a6 0%, #8fa3bd 30%, #2f4d7a 55%, #a9b8cc 80%, #c7d1de 100%);
  }
  .hero-caption {
    position: absolute; left: 200px; top: 340px; width: 458px; height: 98px;
    background: var(--brand-blue); border-radius: 5px; text-align: center; color: #fff;
    padding-top: 12px;
  }
  .hero-caption__title { font-size: 23px; font-weight: 600; line-height: 30px; letter-spacing: 0.01em; }
  .hero-caption__rule { width: 100px; height: 1px; background: #fff; margin: 2px auto 6px; }
  .hero-caption__sub { font-size: 9.5px; font-weight: 500; }

  .plans { position: absolute; top: 475px; left: 0; right: 0; height: 70px; }
  .plan { position: absolute; top: 0; display: flex; align-items: center; }
  .plan__rate {
    width: 66px; height: 66px; border: 2.5px solid var(--brand-blue); border-radius: 50%;
    display: flex; align-items: center; justify-content: center;
    font-family: "Oswald", sans-serif; font-size: 26px; color: var(--brand-blue); font-weight: 500;
  }
  .plan__text { margin-left: 11px; }
  .plan__name { font-size: 15.5px; font-weight: 600; color: var(--brand-blue); }
  .plan__note { font-size: 10px; color: var(--soft-grey); margin-top: 3px; }

  /* back */
  .services-head { position: absolute; left: 52px; top: 38px; }
  .services-head__title { font-size: 23px; font-weight: 700; color: var(--brand-blue); letter-spacing: 0.01em; }
  .services-head__sub { font-size: 13px; color: var(--soft-grey); line-height: 17px; margin-top: 4px; }

  .service { position: absolute; display: flex; align-items: center; }
  .service__icon {
    width: 70px; height: 70px; border: 2.5px solid var(--brand-blue); border-radius: 50%;
    display: flex; align-items: center; justify-content: center;
  }
  .service__icon svg { width: 42px; height: 42px; fill: var(--brand-blue); }
  .service__label { margin-left: 10px; font-size: 15.5px; color: var(--ink-grey); line-height: 19px; }

  .postage-permit {
    position: absolute; left: 705px; top: 72px; width: 101px; height: 101px;
    border: 1px solid #333; font-family: Arial, sans-serif; font-size: 13px;
    line-height: 16px; text-align: center; color: #111; padding-top: 9px;
  }
  .address-window { position: absolute; left: 533px; top: 204px; width: 274px; height: 71px; border: 1.5px solid #222; }

  .postcard--back .wordmark { left: 520px; top: 410px; width: 296px; }
  .postcard--back .wordmark__name { font-size: 29px; letter-spacing: 0.12em; }
  .postcard--back .wordmark__tag { font-size: 14.5px; margin-top: 7px; letter-spacing: 0.2em; }

  .contact-bar {
    position: absolute; left: 0; top: 497px; width: 362px; height: 40px;
    background: var(--brand-blue); color: #fff; font-size: 22px; font-weight: 600;
    padding-left: 52px; line-height: 40px;
  }
  .contact-details { position: absolute; left: 381px; top: 503px; font-size: 11.5px; color: var(--ink-grey); line-height: 18px; }
  .contact-details .sep { margin: 0 10px; }
</style>
</head>
<body>

<section class="postcard postcard--front">
  <div class="wordmark">
    <span class="wordmark__name">BRAMBLECREST</span>
    <span class="wordmark__tag">PROPERTY MANAGEMENT</span>
  </div>
  <div class="hero-photo" role="img" aria-label="Photo of two smiling businessmen in suits reviewing a laptop on a sofa by an office window with a city view"></div>
  <div class="hero-caption">
    <div class="hero-caption__title">CHOOSE THE RIGHT PROPERTY<br>MANAGEMENT SYSTEM</div>
    <div class="hero-caption__rule"></div>
    <div class="hero-caption__sub">SELECTING THE WRONG MANAGER COULD BE YOUR COSTLIEST MISTAKE EVE</div>
  </div>
  <div class="plans">
    <div class="plan" style="left:61px">
      <div class="plan__rate">9%</div>
      <div class="plan__text"><div class="plan__name">LEASE ONLY</div><div class="plan__note">You Just Need Tenants</div></div>
    </div>
    <div class="plan" style="left:315px">
      <div class="plan__rate">10%</div>
      <div class="plan__text"><div class="plan__name">FULL SERVICE</div><div class="plan__note">Our Most Popular</div></div>
    </div>
    <div class="plan" style="left:566px">
      <div class="plan__rate">12%</div>
      <div class="plan__text"><div class="plan__name">PREMIUM SERVICE</div><div class="plan__note">Our Premier Service</div></div>
    </div>
  </div>
</section>

<section class="postcard postcard--back">
  <div class="services-head">
    <div class="services-head__title">DISCOVER OUR SERVICES</div>
    <div class="services-head__sub">WE OFFER FULL-SERVICE PROPERTY<br>MANAGEMENT SOLUTIONS</div>
  </div>

  <div class="service" style="left:49px;top:120px">
    <div class="service__icon"><svg viewBox="0 0 24 24"><path d="M12 3 2 12h3v9h5v-6h4v6h5v-9h3z"/></svg></div>
    <div class="service__label">Property<br>Marketing</div>
  </div>
  <div class="service" style="left:278px;top:120px">
    <div class="service__icon"><svg viewBox="0 0 24 24"><path d="M10 2a8 8 0 0 1 6.3 12.9l5.4 5.4-1.4 1.4-5.4-5.4A8 8 0 1 1 10 2zm0 2a6 6 0 1 0 0 12 6 6 0 0 0 0-12z"/><circle cx="10" cy="10" r="5"/></svg></div>
    <div class="service__label">Property<br>Inspections</div>
  </div>

  <div class="service" style="left:49px;top:208px">
    <div class="service__icon"><svg viewBox="0 0 24 24"><circle cx="9" cy="7" r="4"/><circle cx="16.5" cy="8" r="3.2"/><path d="M1 21c0-4.5 3.6-7 8-7s8 2.5 8 7z"/><path d="M17 13.5c3.5 0 6 2 6 6h-4.5c0-2.3-.6-4.3-1.5-6z"/></svg></div>
    <div class="service__label">Tenant<br>Screening</div>
  </div>
  <div class="service" style="left:278px;top:208px">
    <div class="service__icon"><svg viewBox="0 0 24 24"><rect x="3" y="12" width="3" height="9"/><rect x="8" y="9" width="3" height="12"/><rect x="13" y="11" width="3" height="10"/><rect x="18" y="7" width="3" height="14"/><path d="M3 9l5-4 5 3 7-5" stroke="#1f5b93" stroke-width="1.6" fill="none"/></svg></div>
    <div class="service__label">Financial<br>Reporting</div>
  </div>

  <div class="service" style="left:49px;top:296px">
    <div class="service__icon"><svg viewBox="0 0 24 24"><path d="M12 2 1 12h3v10h16V12h3z"/><text x="12" y="19.5" font-family="Montserrat, sans-serif" font-size="10" font-weight="700" fill="#fff" text-anchor="middle">$</text></svg></div>
    <div class="service__label">Rent<br>Collection</div>
  </div>
  <div class="service" style="left:278px;top:296px">
    <div class="service__icon"><svg viewBox="0 0 24 24"><rect x="11" y="3" width="2" height="16"/><rect x="7" y="19" width="10" height="2"/><rect x="3" y="5" width="18" height="1.6"/><path d="M5 6 2 13h6zM19 6l-3 7h6z"/><path d="M1.5 13.5h7a3.5 3 0 0 1-7 0zM15.5 13.5h7a3.5 3 0 0 1-7 0z"/></svg></div>
    <div class="service__label">Legal<br>Guidance</div>
  </div>

  <div class="service" style="left:49px;top:384px">
    <div class="service__icon"><svg viewBox="0 0 24 24"><path d="M14.5 2a5 5 0 0 0-4.8 6.4L2 16.1 5.9 20l7.7-7.7A5 5 0 0 0 20 7.5l-3 3-3.5-1-1-3.5 3-3a5 5 0 0 0-1-.5z"/></svg></div>
    <div class="service__label">Maintenance</div>
  </div>
  <div class="service" style="left:278px;top:384px">
    <div class="service__icon"><svg viewBox="0 0 24 24"><path d="M12 2 3 5v6c0 5.5 3.8 10 9 11 5.2-1 9-5.5 9-11V5zm0 2.2v15.6c-3.9-1-7-4.6-7-8.8V6.4z"/></svg></div>
    <div class="service__label">Evictions</div>
  </div>

  <div class="postage-permit">PRSRT STD<br>ECRWSS<br>U.S.POSTAGE<br>PAID<br>EDDM RETAIL</div>
  <div class="address-window"></div>

  <div class="wordmark">
    <span class="wordmark__name">BRAMBLECREST</span>
    <span class="wordmark__tag">PROPERTY MANAGEMENT</span>
  </div>

  <div class="contact-bar">CONTACT OUR TEAM</div>
  <div class="contact-details">
    www.bramblecrestpm.com<span class="sep">|</span>(806) 555-0147<span class="sep">|</span>info@bramblecrestpm.com<br>
    2387 Hollow Pine Road, Lubbock, TX 79852
  </div>
</section>

</body>
</html>
```